RB Halden Electric Yard Sign

Looking to have a yard sign designed that we can place at projects we are working on. Most likely will be 18" H x 24" W but flexible that we can increase the size if necessary. It should include our logo, our phone # 609-555-0147, website rbhaldenelectric.example and slogan, built on integrity, driven by excellence. Colors should match our brand.

```html
<!DOCTYPE html>
<html lang="en">
<head>
<meta charset="utf-8">
<title>RB Halden Electric Yard Sign</title>
<link rel="stylesheet" href="https://fonts.googleapis.com/css2?family=Montserrat:wght@500;700&display=swap">
<style>
  :root {
    --brand-red: #ec2028;
    --brand-navy: #15315e;
    --sign-white: #ffffff;
  }
  html, body {
    margin: 0;
    padding: 0;
    width: 1200px;
    height: 877px;
    overflow: hidden;
    background: var(--sign-white);
  }
  .yard-sign {
    position: relative;
    width: 1200px;
    height: 877px;
    background: var(--sign-white);
    font-family: "Montserrat", Arial, sans-serif;
  }
  .accent-bands {
    position: absolute;
    inset: 0;
  }
  .content {
    position: absolute;
    left: 106px;
    right: 0;
    top: 0;
    text-align: center;
  }
  .brand-name {
    position: absolute;
    left: 0;
    right: 0;
    top: 205px;
    margin: 0;
    display: flex;
    justify-content: center;
    align-items: center;
    gap: 22px;
    font-size: 74px;
    font-weight: 700;
    color: var(--brand-red);
    letter-spacing: 1px;
  }
  .brand-dot {
    width: 40px;
    height: 40px;
    border-radius: 50%;
    background: var(--brand-navy);
    flex: none;
  }
  .phone {
    position: absolute;
    left: 0;
    right: 0;
    top: 465px;
    margin: 0;
    font-size: 138px;
    line-height: 1;
    font-weight: 700;
    color: var(--brand-navy);
    letter-spacing: -2px;
  }
  .website {
    position: absolute;
    left: 0;
    right: 0;
    top: 670px;
    margin: 0;
    font-size: 45px;
    font-weight: 500;
    color: var(--brand-navy);
  }
  .slogan {
    position: absolute;
    left: 0;
    right: 0;
    top: 796px;
    margin: 0;
    font-size: 40px;
    font-weight: 700;
    color: var(--sign-white);
  }
</style>
</head>
<body>
  <main class="yard-sign">
    <svg class="accent-bands" width="1200" height="877" viewBox="0 0 1200 877" aria-hidden="true">
      <polygon class="band-red-stripe" points="0,0 118,0 18,877 0,877" fill="var(--brand-red)"/>
      <polygon class="band-navy-stripe" points="118,0 180,0 80,877 18,877" fill="var(--brand-navy)"/>
      <polygon class="slogan-bar" points="92,772 1200,772 1200,877 80,877" fill="var(--brand-red)"/>
    </svg>
    <section class="content">
      <h1 class="brand-name"><span class="brand-dot"></span>RB Halden Electric</h1>
      <p class="phone">609-555-0147</p>
      <p class="website">www.rbhaldenelectric.example</p>
      <p class="slogan">Built on Integrity, Driven by Excellence.</p>
    </section>
  </main>
</body>
</html>
```